PROPERTY MANAGEMENT AND REAL ESTATE

Target Market(s)

real estate owners and investors

Industry/Entity Type

Real Estate

Contact Information for Business Card

BRIGHT LANTERN PROPERTY MANAGEMENT GROUP, LLC
287 North Willowmere Parkway
Suite 240
Hallandale Beach, FL 33071

```html
<!DOCTYPE html>
<html lang="en">
<head>
<meta charset="utf-8">
<title>Bright Lantern Property Management Group – Business Card</title>
<link rel="stylesheet" href="https://fonts.googleapis.com/css2?family=Josefin+Sans:wght@400;600&display=swap">
<style>
  :root {
    --page-bg: #e9e6e0;
    --card-white: #ffffff;
    --card-shade: #eeeeee;
    --ink: #2b2b2b;
    --panel-black: #050505;
    --accent-red: #8e1516;
    --on-dark: #ffffff;
  }
  * { margin: 0; padding: 0; box-sizing: border-box; }
  html, body {
    width: 1200px; height: 899px; overflow: hidden;
    background: var(--page-bg);
    font-family: "Josefin Sans", sans-serif;
    color: var(--ink);
  }
  .business-card {
    position: absolute; left: 75px; top: 150px;
    width: 1050px; height: 600px;
    background: radial-gradient(ellipse at 40% 40%, var(--card-white) 0%, var(--card-shade) 100%);
    box-shadow: 0 10px 30px rgba(0,0,0,0.18);
    overflow: hidden;
  }
  .side-panel { position: absolute; inset: 0; width: 1050px; height: 600px; }
  .brand {
    position: absolute; left: 60px; top: 70px;
    display: flex; align-items: center; gap: 26px;
  }
  .brand-mark {
    width: 120px; height: 120px; border-radius: 50%;
    background: var(--accent-red); flex: none;
  }
  .brand-name {
    font-size: 27px; font-weight: 400; line-height: 1.12;
    letter-spacing: 0.5px; color: var(--ink); max-width: 460px;
  }
  .address {
    position: absolute; left: 60px; top: 300px;
    font-size: 24px; line-height: 1.3; letter-spacing: 1px;
  }
  .contact-list {
    position: absolute; left: 100px; top: 380px;
    list-style: none; font-size: 22px; letter-spacing: 1px;
  }
  .contact-list li { display: flex; align-items: center; gap: 16px; height: 38px; }
  .contact-list svg { width: 20px; height: 20px; fill: var(--accent-red); flex: none; }
  .person {
    position: absolute; right: 34px; top: 320px;
    text-align: right; color: var(--on-dark);
  }
  .person-name { font-size: 28px; font-weight: 600; letter-spacing: 1px; white-space: nowrap; }
  .person-role { font-size: 18px; letter-spacing: 1.5px; margin-top: 6px; white-space: nowrap; }
</style>
</head>
<body>
  <section class="business-card">
    <svg class="side-panel" viewBox="0 0 1050 600" aria-hidden="true">
      <path d="M 804 0 Q 580 300 836 600 L 1050 600 L 1050 0 Z" fill="var(--accent-red)"/>
      <path d="M 818 0 Q 596 300 850 600 L 1050 600 L 1050 0 Z" fill="var(--panel-black)"/>
    </svg>

    <header class="brand">
      <span class="brand-mark"></span>
      <h1 class="brand-name">BRIGHT LANTERN PROPERTY MANAGEMENT GROUP, LLC</h1>
    </header>

    <p class="address">287 North Willowmere Parkway<br>Suite 240, Hallandale Beach, FL 33071</p>

    <ul class="contact-list">
      <li>
        <svg viewBox="0 0 24 24"><path d="M6.6 10.8c1.4 2.8 3.8 5.1 6.6 6.6l2.2-2.2c.3-.3.7-.4 1-.2 1.1.4 2.3.6 3.6.6.6 0 1 .4 1 1V20c0 .6-.4 1-1 1C10.6 21 3 13.4 3 4c0-.6.4-1 1-1h3.5c.6 0 1 .4 1 1 0 1.2.2 2.4.6 3.6.1.3 0 .7-.2 1z"/></svg>
        954 555 0142
      </li>
      <li>
        <svg viewBox="0 0 24 24"><path d="M7 1h10a2 2 0 0 1 2 2v18a2 2 0 0 1-2 2H7a2 2 0 0 1-2-2V3a2 2 0 0 1 2-2zm0 3v14h10V4zm5 15.5a1 1 0 1 0 0 2 1 1 0 0 0 0-2z"/></svg>
        954 555 0187
      </li>
      <li>
        <svg viewBox="0 0 24 24"><path d="M7 2h8l3 3v5h2a2 2 0 0 1 2 2v8a2 2 0 0 1-2 2H4a2 2 0 0 1-2-2v-8a2 2 0 0 1 2-2h3zm2 2v6h7V6h-2V4zm-3 10v2h2v-2zm4 0v2h2v-2zm4 0v2h2v-2z"/></svg>
        954 555 0163
      </li>
      <li>
        <svg viewBox="0 0 24 24"><path d="M2 5h20v14H2zm2 2v.5l8 5.5 8-5.5V7zm0 3v7h16v-7l-8 5.5z"/></svg>
        office@brightlanternpm.com
      </li>
      <li>
        <svg viewBox="0 0 24 24"><path d="M12 2a10 10 0 1 0 0 20 10 10 0 0 0 0-20zm6.9 9h-3c-.1-2.3-.6-4.3-1.4-5.8A8 8 0 0 1 18.9 11zM12 4c.8 1 1.8 3.4 1.9 7h-3.8C10.2 7.4 11.2 5 12 4zM9.5 5.2C8.7 6.7 8.2 8.7 8.1 11h-3a8 8 0 0 1 4.4-5.8zM5.1 13h3c.1 2.3.6 4.3 1.4 5.8A8 8 0 0 1 5.1 13zM12 20c-.8-1-1.8-3.4-1.9-7h3.8c-.1 3.6-1.1 6-1.9 7zm2.5-1.2c.8-1.5 1.3-3.5 1.4-5.8h3a8 8 0 0 1-4.4 5.8z"/></svg>
        www.brightlanternpm.com
      </li>
    </ul>

    <div class="person">
      <p class="person-name">JORDAN WESTLEY</p>
      <p class="person-role">FINANCIAL ADVISOR</p>
    </div>
  </section>
</body>
</html>
```